Brightway Haus Inc. Business Card Design

Brightway Haus Inc. is in search of a great clean design for our business cards!

Looking to incorporate our full logo and watermark on side one (however, I am open to having the text and watermark separated within the design.)

On side two, I am looking to have contact information (Name, Position, Phone #, Email, Website (www.thebrightwayhaus.ca). Can have the logo and/or watermark as part of the design if applicable.

Please add tagline "Where Shine Counts" on either side 1 or 2. This tagline can be in a sans serif, serif or cursive font as long as it compliments overall design. Capitalization can be title or sentence case depending on how it fits within the design.

Get creative!! Looking for a clean, crisp, premium design! Looking for a glossy card finish with spot UV features when printed. Cards will also be printed with rounded corners. Standard dimensions (3.5 x 2).

Target Market(s)

B2B - primary clients are business owners or property management corporations. (residential jobs are few and far between)

Industry/Entity Type

Business

Contact Information for Business Card

- clean, crisp design
- double sided
- spot UV accents and glossy finish upon printing
- standard business card size (3.5 x 2) with rounded corners
- please see project description for requirements per side

Font styles to use
Sans Serif

Requirements
Must have
• - adequate bleeds with print ready files
• - cohesive design elements between side 1 & 2
• - spot UV elements (can be on both sides or just one, use your discretion)
• - colour pallet should match the logo file provided
• - incorporate tagline "where shine counts" (this tagline can be in a serif or sans serif font as long as it is complimentary to the overall design.
Nice to have
• - Premium elements with a clean design
Should not have
• - Please omit cartoon or whimsical like designs, think premium.
• - Colours should not stray from the pallet of the provided logo.

```html
<!DOCTYPE html>
<html lang="en">
<head>
<meta charset="utf-8">
<title>Brightway Haus Inc. Business Cards</title>
<link rel="stylesheet" href="https://fonts.googleapis.com/css2?family=Open+Sans:wght@700&family=Roboto:wght@400;500&family=Roboto+Condensed:wght@700&display=swap">
<style>
  :root {
    --backdrop: #2b2b2b;
    --card: #f4f4f4;
    --teal: #13aeb0;
    --navy: #1d2456;
    --grey-text: #4e4e4e;
    --rule: #9a9a9a;
    --watermark: #dcecee;
  }
  * { margin: 0; padding: 0; box-sizing: border-box; }
  html, body { width: 1200px; height: 960px; overflow: hidden; }
  body { background: var(--backdrop); position: relative; font-family: "Roboto", Arial, sans-serif; }

  .card {
    position: absolute; width: 600px; height: 342px;
    background: var(--card); border-radius: 22px; overflow: hidden;
  }
  .card--front { left: 314px; top: 114px; }
  .card--back { left: 311px; top: 472px; }

  .wordmark {
    position: absolute; left: 0; right: 0; text-align: center;
    font-family: "Open Sans", Arial, sans-serif; font-weight: 700;
    color: var(--navy); letter-spacing: -0.5px; white-space: nowrap;
  }
  .card--front .wordmark { top: 86px; font-size: 38px; }

  .contact-person {
    position: absolute; right: 320px; top: 186px; text-align: right;
    color: var(--grey-text); font-size: 14.5px; line-height: 19px;
  }
  .contact-person__name {
    font-family: "Roboto Condensed", Arial, sans-serif; font-weight: 700;
    color: var(--teal); font-size: 21px; line-height: 24px;
  }
  .contact-person__role {
    font-family: "Roboto Condensed", Arial, sans-serif; font-weight: 700;
    color: var(--navy); font-size: 15px; line-height: 19px;
  }
  .contact-divider {
    position: absolute; left: 300px; top: 184px; width: 1px; height: 82px; background: var(--rule);
  }
  .contact-list {
    position: absolute; left: 322px; top: 189px; list-style: none;
    color: var(--grey-text); font-size: 14.5px; line-height: 19.3px;
  }
  .contact-list li { display: flex; align-items: center; gap: 9px; }
  .contact-list svg { width: 13px; height: 13px; fill: var(--teal); flex: none; }

  .colour-band { position: absolute; bottom: 0; height: 13px; }
  .colour-band--teal { left: 0; width: 298px; background: var(--teal); }
  .colour-band--navy { left: 301px; right: 0; background: var(--navy); }

  .watermark-square {
    position: absolute; left: 170px; top: 26px; width: 290px; height: 290px;
    background: var(--watermark); opacity: 0.7;
  }
  .card--back .wordmark { top: 128px; font-size: 44px; }
  .tagline {
    position: absolute; left: 0; right: 0; top: 195px; text-align: center;
    font-size: 14px; letter-spacing: 9px; color: var(--grey-text);
  }
</style>
</head>
<body>
  <section class="card card--front">
    <div class="wordmark">BRIGHTWAY HAUS INC.</div>

    <div class="contact-person">
      <div class="contact-person__name">MARA LINDQVIST</div>
      <div class="contact-person__role">CEO/FOUNDER</div>
      <div>2140 Cedarfield Road</div>
      <div>Fairbanks, Alaska 99701</div>
    </div>
    <div class="contact-divider"></div>
    <ul class="contact-list">
      <li><svg viewBox="0 0 24 24"><path d="M6.6 10.8a15.1 15.1 0 0 0 6.6 6.6l2.2-2.2c.3-.3.7-.4 1-.2 1.1.4 2.3.6 3.6.6.6 0 1 .4 1 1V20c0 .6-.4 1-1 1A17 17 0 0 1 3 4c0-.6.4-1 1-1h3.5c.6 0 1 .4 1 1 0 1.3.2 2.5.6 3.6.1.3 0 .7-.2 1z"/></svg>907 512 3846</li>
      <li><svg viewBox="0 0 24 24"><path d="M7 1h10a2 2 0 0 1 2 2v18a2 2 0 0 1-2 2H7a2 2 0 0 1-2-2V3a2 2 0 0 1 2-2zm0 3v14h10V4zm5 15.5a1 1 0 1 0 0 2 1 1 0 0 0 0-2z"/></svg>907 274 6190</li>
      <li><svg viewBox="0 0 24 24"><path d="M6 2h12v6H6zM3 9h18a2 2 0 0 1 2 2v7h-4v4H5v-4H1v-7a2 2 0 0 1 2-2zm4 7v4h10v-4z"/></svg>907 388 5027</li>
      <li><svg viewBox="0 0 24 24"><path d="M2 5h20v14H2zm2 2v.5l8 5 8-5V7z"/></svg>hello@brightwayhaus.ca</li>
    </ul>

    <div class="colour-band colour-band--teal"></div>
    <div class="colour-band colour-band--navy"></div>
  </section>

  <section class="card card--back">
    <div class="watermark-square" role="img" aria-label="Faint brand watermark area"></div>
    <div class="wordmark">BRIGHTWAY HAUS INC.</div>
    <div class="tagline">Where Shine Counts</div>
  </section>
</body>
</html>
```